New Company Business Card design

Looking for a corporate looking business card utilising my new logo design - the logo i would like embossed as one option and flat as another - simplistic but stylish - less is more - we are an import export business launching into the market - i would like a couple of options as main background - Grey or Black

```html
<!DOCTYPE html>
<html lang="en">
<head>
<meta charset="utf-8">
<title>Norvale Trade Partners – Business Card</title>
<link rel="stylesheet" href="https://fonts.googleapis.com/css2?family=Crimson+Text:wght@400;600&display=swap">
<style>
  :root {
    --stage: #d4d4d4;
    --card-dark: #333333;
    --card-light: #f0f0f0;
    --brand-blue: #1e7fd0;
    --text-light: #f2f2f2;
    --icon-grey: #8a8a8a;
  }
  * { box-sizing: border-box; margin: 0; padding: 0; }
  html, body { width: 1200px; height: 1200px; overflow: hidden; }
  body {
    background: var(--stage);
    font-family: "Crimson Text", Georgia, serif;
    position: relative;
  }
  .card {
    position: absolute;
    left: 292px;
    width: 570px;
    height: 341px;
    background: var(--card-dark);
    box-shadow: 0 2px 6px rgba(0,0,0,0.25);
  }
  .card--front { top: 122px; }
  .card--back { top: 685px; display: flex; }

  .brand {
    display: flex;
    align-items: center;
    gap: 10px;
    color: var(--brand-blue);
    font-weight: 600;
    letter-spacing: 0.04em;
    white-space: nowrap;
  }
  .brand__dot {
    border-radius: 50%;
    background: var(--brand-blue);
    flex: none;
  }
  .card--front .brand {
    position: absolute;
    left: 50%; top: 50%;
    transform: translate(-50%, -50%);
    font-size: 30px;
  }
  .card--front .brand__dot { width: 22px; height: 22px; }

  .back__info {
    position: relative;
    width: 356px;
    height: 100%;
    background: var(--card-dark);
  }
  .back__info .brand {
    position: absolute;
    left: 25px; top: 78px;
    font-size: 18px;
  }
  .back__info .brand__dot { width: 14px; height: 14px; }

  .holder {
    position: absolute;
    left: 0; right: 0; top: 148px;
    text-align: center;
    padding-left: 20px;
    color: var(--text-light);
    font-size: 21px;
  }

  .contacts {
    position: absolute;
    left: 26px; top: 200px;
    list-style: none;
    color: var(--text-light);
    font-size: 19px;
    line-height: 1;
  }
  .contacts li {
    display: flex;
    align-items: center;
    gap: 8px;
    height: 28px;
  }
  .contacts svg { width: 22px; height: 22px; flex: none; }

  .back__mark {
    flex: 1;
    background: var(--card-light);
    position: relative;
  }
  .back__mark .brand {
    position: absolute;
    left: 50%; top: 262px;
    transform: translate(-50%, -50%);
    font-size: 15px;
    gap: 7px;
  }
  .back__mark .brand__dot { width: 12px; height: 12px; }
</style>
</head>
<body>

<section class="card card--front" aria-label="Card front">
  <div class="brand"><span class="brand__dot"></span>Norvale Trade Partners</div>
</section>

<section class="card card--back" aria-label="Card back">
  <div class="back__info">
    <div class="brand"><span class="brand__dot"></span>Norvale Trade Partners</div>
    <p class="holder">Mr. Dalen Morrow, Director</p>
    <ul class="contacts">
      <li>
        <svg viewBox="0 0 22 22" aria-hidden="true"><rect x="6" y="1" width="10" height="20" rx="1.5" fill="var(--icon-grey)"/><rect x="9" y="2.5" width="4" height="1" fill="var(--brand-blue)"/></svg>
        ++ 555 210
      </li>
      <li>
        <svg viewBox="0 0 22 22" aria-hidden="true"><circle cx="11" cy="11" r="9.5" fill="none" stroke="var(--brand-blue)" stroke-width="1.5"/><path d="M8 6.5c-1 .6-1.3 1.8-.8 3.2.8 2.3 2.6 4.3 4.7 5.3 1.3.6 2.4.4 3.1-.5l-1.6-1.6-1.3.7c-1.2-.6-2.1-1.6-2.7-2.8l.7-1.3z" fill="var(--brand-blue)"/></svg>
        ++ 555 347
      </li>
      <li>
        <svg viewBox="0 0 22 22" aria-hidden="true"><path d="M11 2 1.5 11H4v9h5v-6h4v6h5v-9h2.5z" fill="var(--brand-blue)"/></svg>
        norvaletrade.com
      </li>
      <li>
        <svg viewBox="0 0 22 22" aria-hidden="true"><rect x="1" y="5" width="20" height="13" fill="var(--brand-blue)"/><path d="M1 5l10 8 10-8" fill="none" stroke="var(--card-dark)" stroke-width="1.2"/></svg>
        hello@norvaletrade.com
      </li>
    </ul>
  </div>
  <div class="back__mark">
    <div class="brand"><span class="brand__dot"></span>Norvale Trade Partners</div>
  </div>
</section>

</body>
</html>
```